Business Card for Coastal Tundrabridge Advisory

We need a business card for Coastal Tundrabridge Advisory. The company website address is provided below. The company logo is attached. We provide specialized permafrost services to the mining, transportation, and oil & gas industries. The card should be prepared for:
Matthias Korhonen, PhD.
Coastal Tundrabridge Advisory
PO Box 418259
Quillwater, Alaska 99642
Direct: +1-907-555-0143
Email: mkorhonen@tundrabridgeadvisory.example
Website: www.coastaltundrabridgeadvisory.example

```html
<!DOCTYPE html>
<html lang="en">
<head>
<meta charset="utf-8">
<title>Coastal Tundrabridge Advisory – Business Card</title>
<link href="https://fonts.googleapis.com/css2?family=Open+Sans:wght@400;600;700&display=swap" rel="stylesheet">
<style>
  :root {
    --backdrop: #d9d9d9;
    --card: #ffffff;
    --ink: #1b232d;
    --ink-soft: #555a60;
    --rule: #9a9ea3;
  }
  * { box-sizing: border-box; margin: 0; padding: 0; }
  html, body {
    width: 1200px; height: 900px; overflow: hidden;
    background: var(--backdrop);
    font-family: "Open Sans", Arial, sans-serif;
    color: var(--ink);
  }
  .stage {
    width: 1200px; height: 900px;
    display: flex; flex-direction: column;
    align-items: center; justify-content: center;
    gap: 36px;
  }
  .card {
    position: relative;
    width: 700px; height: 400px;
    background: var(--card);
    box-shadow: 0 6px 18px rgba(0,0,0,0.18);
  }
  .brand-name {
    font-weight: 700;
    color: var(--ink);
    letter-spacing: 0.5px;
    white-space: nowrap;
  }
  /* Front */
  .card-front .brand-name {
    position: absolute; left: 0; right: 0; top: 150px;
    text-align: center; font-size: 36px;
  }
  .tagline {
    position: absolute; left: 300px; right: 40px; top: 290px;
    text-align: center; font-size: 15px; line-height: 1.4;
    font-weight: 600; color: var(--ink);
  }
  /* Back */
  .card-back .brand-name {
    position: absolute; right: 40px; top: 48px;
    font-size: 27px;
  }
  .contact {
    position: absolute; left: 44px; bottom: 40px; width: 470px;
  }
  .person-name {
    font-size: 21px; font-weight: 700; text-transform: uppercase;
    letter-spacing: -0.3px;
  }
  .person-company {
    font-size: 17px; color: var(--ink-soft); margin-bottom: 22px;
  }
  .contact-list { list-style: none; }
  .contact-list li {
    display: flex; align-items: center; gap: 10px;
    font-size: 16px; color: var(--ink-soft); line-height: 1.7;
  }
  .contact-list svg { width: 16px; height: 16px; flex: none; }
  .address {
    margin-top: 8px; padding-top: 8px;
    border-top: 1px solid var(--rule);
    font-size: 16px; color: var(--ink-soft);
  }
</style>
</head>
<body>
<main class="stage">
  <section class="card card-front" aria-label="Card front">
    <div class="brand-name">Coastal Tundrabridge Advisory</div>
    <p class="tagline">We Provide Specialized Permafrost Services To The Mining, Transportation, And Oil &amp; Gas Industries</p>
  </section>

  <section class="card card-back" aria-label="Card back">
    <div class="brand-name">Coastal Tundrabridge Advisory</div>
    <div class="contact">
      <div class="person-name">Matthias Korhonen, PhD.</div>
      <div class="person-company">Coastal Tundrabridge Advisory</div>
      <ul class="contact-list">
        <li>
          <svg viewBox="0 0 16 16" aria-hidden="true"><path d="M4 1.5l2.2 3-1.3 1.6c.8 1.8 2.2 3.2 4 4l1.6-1.3 3 2.2-1 2.5c-5.8-.4-10.1-4.7-10.5-10.5z" fill="#1b232d"/></svg>
          +1-907-555-0143
        </li>
        <li>
          <svg viewBox="0 0 16 16" aria-hidden="true"><rect x="1" y="3" width="14" height="10" fill="#1b232d"/><path d="M1.5 3.5L8 9l6.5-5.5" stroke="#fff" stroke-width="1.2" fill="none"/></svg>
          mkorhonen@tundrabridgeadvisory.example
        </li>
        <li>
          <svg viewBox="0 0 16 16" aria-hidden="true"><g fill="none" stroke="#1b232d" stroke-width="1.2"><circle cx="8" cy="8" r="6.5"/><ellipse cx="8" cy="8" rx="3" ry="6.5"/><path d="M1.5 8h13M2.5 4.8h11M2.5 11.2h11"/></g></svg>
          www.coastaltundrabridgeadvisory.example
        </li>
      </ul>
      <div class="address">PO Box 418259, Quillwater, Alaska 99642</div>
    </div>
  </section>
</main>
</body>
</html>
```